Profesional personal website needs design and business card

I need a business card with my professional name as a logo "Dorian Vitality" for my business. I am a Wellness Coach, consultant and trainer. So it should be professional, wellness oriented and modern.

Target Market(s)

Private clients, governments, corporations. Luxury and high market.

Industry/Entity Type

Health And Wellness

Contact Information for Business Card

Dorian Vitality should be the logo

Colors

Designer to choose colors to be used in the design.

Requirements
Must have
• Dorian Vitality
• Name: Tomás Lirandel
• Wellness Coach, Consultant & Trainer.
• Website: www.dorianvitality-example.com
• Phone:
• Spain (+34) 612 480 317
• (USA) +1 (555) 610 4829
Nice to have
• The most important is the design of "Dorian Vitality", as this is going to be my personal brand logo. It should be professional, wellness, high end and actual.
Should not have
• no golds, no baroque style..

```html
<!DOCTYPE html>
<html lang="en">
<head>
<meta charset="UTF-8">
<title>Dorian Vitality — Business Card</title>
<link href="https://fonts.googleapis.com/css2?family=Lato:wght@400;700&display=swap" rel="stylesheet">
<style>
  :root {
    --brand-blue: #01719a;
    --ink: #1f2326;
    --muted: #4a4f55;
    --paper: #ffffff;
    --page: #ffffff;
    --shadow: rgba(0, 0, 0, 0.28);
  }
  * { margin: 0; padding: 0; box-sizing: border-box; }
  html, body {
    width: 1200px; height: 1200px; overflow: hidden;
    background: var(--page);
    font-family: "Lato", sans-serif;
  }
  .stage { position: relative; width: 1200px; height: 1200px; }
  .card {
    position: absolute; left: 180px; width: 840px;
    box-shadow: 4px 5px 8px var(--shadow);
  }
  .card--front { top: 84px; height: 477px; background: var(--paper); }
  .card--back { top: 639px; height: 479px; background: var(--brand-blue); }

  .wordmark {
    position: absolute;
    font-weight: 700; letter-spacing: 0.01em; white-space: nowrap;
    line-height: 1;
  }
  .card--front .wordmark {
    left: 79px; top: 197px; width: 304px; text-align: center;
    font-size: 40px; color: var(--brand-blue);
  }
  .card--back .wordmark {
    left: 0; width: 100%; top: 214px; text-align: center;
    font-size: 56px; color: var(--paper);
  }

  .divider {
    position: absolute; left: 419px; top: 154px;
    width: 3px; height: 165px; background: var(--brand-blue);
  }
  .details { position: absolute; left: 460px; top: 150px; }
  .details__name {
    font-size: 38px; font-weight: 700; color: var(--brand-blue);
    line-height: 1; letter-spacing: -0.01em;
  }
  .details__role {
    margin-top: 8px; font-size: 19px; color: var(--muted); line-height: 1;
  }
  .contact { list-style: none; margin-top: 20px; }
  .contact__item {
    display: flex; align-items: center; gap: 9px;
    font-size: 19.5px; color: var(--ink); line-height: 1; height: 29px;
  }
  .contact__item svg { width: 18px; height: 18px; fill: var(--brand-blue); flex: none; }
  .contact__tag { color: var(--brand-blue); }

  .back-url {
    position: absolute; left: 0; width: 100%; top: 425px;
    text-align: center; color: var(--paper); font-size: 19.5px;
  }
</style>
</head>
<body>
<main class="stage">
  <section class="card card--front">
    <div class="wordmark">Dorian Vitality</div>
    <div class="divider"></div>
    <div class="details">
      <h1 class="details__name">Tomás Lirandel</h1>
      <p class="details__role">Wellness Coach, Consultant &amp; Trainer</p>
      <ul class="contact">
        <li class="contact__item">
          <svg viewBox="0 0 24 24" aria-hidden="true"><path d="M6.6 10.8a15.1 15.1 0 0 0 6.6 6.6l2.2-2.2c.3-.3.7-.4 1-.2 1.1.4 2.3.6 3.6.6.6 0 1 .4 1 1V20c0 .6-.4 1-1 1A17 17 0 0 1 3 4c0-.6.4-1 1-1h3.5c.6 0 1 .4 1 1 0 1.3.2 2.5.6 3.6.1.3 0 .7-.2 1z"/></svg>
          <span>(+34) 612 480 317 <span class="contact__tag">Spain</span></span>
        </li>
        <li class="contact__item">
          <svg viewBox="0 0 24 24" aria-hidden="true"><path d="M8 2h8a2 2 0 0 1 2 2v16a2 2 0 0 1-2 2H8a2 2 0 0 1-2-2V4a2 2 0 0 1 2-2zm0 3v13h8V5zm4 14.2a1 1 0 1 0 0 2 1 1 0 0 0 0-2z"/></svg>
          <span>+1 (555) 610 4829 <span class="contact__tag">(USA)</span></span>
        </li>
        <li class="contact__item">
          <svg viewBox="0 0 24 24" aria-hidden="true"><path d="M12 2a10 10 0 1 0 0 20 10 10 0 0 0 0-20zm6.9 6h-3a15.7 15.7 0 0 0-1.3-4A8 8 0 0 1 18.9 8zM12 4c.8 1.2 1.5 2.5 1.9 4h-3.8c.4-1.5 1.1-2.8 1.9-4zM4.3 14a8.3 8.3 0 0 1 0-4h3.4a16 16 0 0 0 0 4zm.8 2h3a15.7 15.7 0 0 0 1.3 4A8 8 0 0 1 5.1 16zm3-8h-3a8 8 0 0 1 4.3-4c-.6 1.2-1 2.6-1.3 4zM12 20c-.8-1.2-1.5-2.5-1.9-4h3.8c-.4 1.5-1.1 2.8-1.9 4zm2.3-6H9.7a14 14 0 0 1 0-4h4.6a14 14 0 0 1 0 4zm.3 6c.6-1.2 1-2.6 1.3-4h3a8 8 0 0 1-4.3 4zm1.7-6a16 16 0 0 0 0-4h3.4a8.3 8.3 0 0 1 0 4z"/></svg>
          <span>www.dorianvitality-example.com</span>
        </li>
      </ul>
    </div>
  </section>

  <section class="card card--back">
    <div class="wordmark">Dorian Vitality</div>
    <p class="back-url">www.dorianvitality-example.com</p>
  </section>
</main>
</body>
</html>
```